Brindle Children's Center - Child Care brochure

I just bought a new child care and completely renovated the space. We are also designing a new website, so I need the brochure to match that with updated info. www.brindlechildrenscenter.com - Information on there is current. We expect to have the new one up and running in the next few days. We have new photo's that I'd like to be added to the flyer too. ps. the boys in the pictures are mine, so i would appreciate one of them being added :). support@netcrafterhub.com has details on the website (dev.brindlechildrenscenter.com). The child care program is only open during the ski season - i.e. a resort facility catering to high end clients.
I'm attaching the the website information, the flyer I created, logo files and pictures.

Target Market(s)

Parents of young children

Font styles to use
Other font styles liked:
• "Things we said" & "Calibri Light"

Colors
cfeae6
fef1ee

Requirements
Must have
• Pictures of children. sleek design - winter, mountain theme. Check with website designer on new website.
Nice to have
• prices included
Should not have
• Kid like artwork

```html
<!DOCTYPE html>
<html lang="en">
<head>
<meta charset="utf-8">
<title>Brindle Children's Center – Brochure</title>
<link rel="stylesheet" href="https://fonts.googleapis.com/css2?family=Carlito:wght@400;700&family=Mystery+Quest&display=swap">
<style>
  :root {
    --stage: #b9c2c6;
    --teal: #8fcfcc;
    --teal-soft: rgba(143, 207, 204, 0.72);
    --teal-deep: #2f6f70;
    --ink: #2d3a3d;
    --ink-soft: #4b5658;
    --field: #d9dcdd;
    --white-veil: rgba(255, 255, 255, 0.55);
    --sky-top: #e2eff0;
    --sky-mid: #c4dfe0;
    --sky-low: #a8c6c9;
  }
  * { box-sizing: border-box; margin: 0; padding: 0; }
  html, body { width: 1200px; height: 900px; overflow: hidden; }
  body {
    background: var(--stage);
    font-family: "Carlito", "Calibri", sans-serif;
    color: var(--ink);
    position: relative;
  }
  .brochure {
    position: absolute;
    left: 60px; top: 67px;
    width: 1080px; height: 766px;
    display: flex;
  }
  .panel {
    position: relative;
    width: 360px; height: 100%;
    overflow: hidden;
  }
  .panel + .panel { border-left: 1px solid rgba(255,255,255,0.5); }
  .scenery {
    position: absolute; inset: 0;
    background:
      radial-gradient(ellipse at 40% 20%, rgba(255,255,255,0.7), transparent 55%),
      linear-gradient(180deg, var(--sky-top) 0%, var(--sky-mid) 45%, var(--sky-low) 70%, var(--sky-mid) 100%);
  }
  .display { font-family: "Mystery Quest", cursive; font-weight: 400; }

  /* Left panel */
  .reservations-band {
    position: absolute; left: 0; top: 0; width: 100%; height: 218px;
    background: var(--teal);
    padding: 38px 50px 0 50px;
  }
  .panel-title { font-size: 21px; font-weight: 400; margin-bottom: 14px; }
  .small-copy { font-size: 13.5px; line-height: 1.4; color: var(--ink-soft); text-align: justify; }
  .confirmation {
    position: absolute; left: 0; top: 218px; width: 100%; bottom: 0;
    background: var(--teal-soft);
    padding: 30px 50px 0 50px;
  }
  .field-label { font-size: 13.5px; margin-top: 12px; }
  .field-label:first-of-type { margin-top: 18px; }
  .field {
    width: 232px; height: 22px; margin: 6px 0 0 22px;
    background: var(--field); border-radius: 3px;
  }
  .fee-note { margin-top: 30px; }
  .policy-title { font-size: 13.5px; font-weight: 700; margin-top: 20px; }

  /* Middle panel */
  .rates-title {
    position: absolute; top: 92px; width: 100%; text-align: center;
    font-size: 30px; color: var(--ink);
  }
  .rate-circle {
    position: absolute; border-radius: 50%;
    display: flex; flex-direction: column; align-items: center; justify-content: center;
    text-align: center;
  }
  .rate-circle.daily { left: 38px; top: 120px; width: 282px; height: 282px; background: var(--teal); }
  .rate-circle.season { left: -4px; top: 362px; width: 308px; height: 308px; background: rgba(236, 244, 245, 0.9); }
  .price { font-size: 20px; font-weight: 700; color: var(--teal-deep); }
  .price-note { font-size: 13.5px; color: var(--ink-soft); margin-bottom: 12px; line-height: 1.3; }
  .season-title { font-size: 17px; line-height: 1.3; margin-bottom: 16px; }
  .package-grid { display: grid; grid-template-columns: auto auto; column-gap: 22px; row-gap: 14px; text-align: left; }
  .package-grid .price { font-size: 19px; }
  .package-grid .price-note { font-size: 12.5px; margin: 0; }
  .apres { margin-top: 14px; }

  /* Right panel */
  .name-mark {
    position: absolute; left: 54px; top: 82px; width: 246px; height: 246px;
    border-radius: 50%; background: #ffffff;
    display: flex; align-items: center; justify-content: center; text-align: center;
    font-size: 24px; color: var(--ink); padding: 30px; line-height: 1.25;
  }
  .center-name { position: absolute; top: 358px; width: 100%; text-align: center; font-size: 26px; }
  .ages { position: absolute; top: 400px; width: 100%; text-align: center; font-size: 20px; line-height: 1.3; }
  .hours-band {
    position: absolute; top: 481px; left: 0; width: 100%; height: 90px;
    background: var(--teal); text-align: center; padding-top: 6px;
  }
  .hours-label { font-size: 26px; color: var(--teal-deep); }
  .hours { font-size: 27px; color: #ffffff; }
  .contact { position: absolute; top: 605px; width: 100%; text-align: center; font-size: 14.5px; line-height: 1.45; color: var(--ink-soft); }
  .contact p + p { margin-top: 14px; }
</style>
</head>
<body>
  <main class="brochure">
    <section class="panel panel-reservations">
      <div class="scenery" role="img" aria-label="Photo of snowy mountain peaks in misty winter clouds"></div>
      <div class="reservations-band">
        <h2 class="panel-title">Reservations</h2>
        <p class="small-copy">We highly recommend that reservations be made in advance to ensure space for your child. To make a reservation contact us at: 801-555-0147. We have limited capacity.</p>
      </div>
      <div class="confirmation">
        <h2 class="panel-title">Reservations Conformation</h2>
        <p class="field-label">Conformation Number:</p>
        <div class="field"></div>
        <p class="field-label">Child's Name:</p>
        <div class="field"></div>
        <p class="field-label">Reserved Dates:</p>
        <div class="field"></div>
        <p class="field-label">Reserved Fee:</p>
        <div class="field"></div>
        <p class="small-copy fee-note">* Your reservation fee will be applied to your last day of service.</p>
        <p class="policy-title">Cancellation Policy</p>
        <p class="small-copy">*Reservations must be cancelled 24hrs in advance of the date(s) of service or full fee will be charged for all days not cancelled</p>
      </div>
    </section>

    <section class="panel panel-rates">
      <div class="scenery" role="img" aria-label="Photo of mountain ridge under soft winter clouds"></div>
      <h2 class="rates-title display">Rates</h2>
      <div class="rate-circle daily">
        <p class="price">$109</p><p class="price-note">full day</p>
        <p class="price">$89</p><p class="price-note">half day</p>
        <p class="price">$495</p><p class="price-note">five day package<br>(That's a $50 saving!)</p>
      </div>
      <div class="rate-circle season">
        <p class="season-title">NEW Season Ski<br>Pass Child Care Packages</p>
        <div class="package-grid">
          <div><p class="price">$900</p><p class="price-note">01-20 Full Days</p></div>
          <div><p class="price">$2,700</p><p class="price-note">41-60 Full Days</p></div>
          <div><p class="price">$1,800</p><p class="price-note">21-40 Full Days</p></div>
          <div><p class="price">$3,600</p><p class="price-note">60-80 Full Days</p></div>
        </div>
        <p class="price apres">$30</p><p class="price-note">Après-ski care</p>
      </div>
    </section>

    <section class="panel panel-cover">
      <div class="scenery" role="img" aria-label="Photo of snowy peaks fading into winter mist"></div>
      <div class="name-mark display">Brindle Children's Center</div>
      <h1 class="center-name display">Brindle Children's Center</h1>
      <p class="ages">Serving children ages<br>6 wks thru 9 years</p>
      <div class="hours-band">
        <p class="hours-label display">Open daily</p>
        <p class="hours">8:30-4:30</p>
      </div>
      <div class="contact">
        <p>P.O. Box 4127<br>Brindle, Utah 84000</p>
        <p>(801) 555-0147</p>
        <p>info@brindlechildrenscenter.com</p>
      </div>
    </section>
  </main>
</body>
</html>
```